Bootstrap Website for Sports Technology Company

Create Bootstrap compatible, HTML and CSS stylesheet-based design templates for typography, forms, buttons, charts, navigation and other interface components for the www.tallow-pinery.com website. All designs should be Responsive CSS and Fluid.
We are transitioning www.tallow-pinery.com from Wordpress to Bootstrap and are looking for a fresh, clean landing page with navigation to other page styles. Official Colors and font are attached. Designer may recommend button styles, menu navigation, header, footer, etc. Please incorporate the graphic elements found on the tallow-pinery.com website.
Page Styles required:
- Landing Page
- Secondary Landing Page
- Five different Page Styles
- small, medium and large buttons
Designers are encouraged to submit the landing page with navigation. We will comment quickly to help with finalizing the design for final selection.
Industry/Entity Type
It Company
Look and feel
Each slider illustrates characteristics of the customer's brand and the style your logo design should communicate.

```html
<!DOCTYPE html>
<html lang="en">
<head>
<meta charset="utf-8">
<title>Tallow Pinery – World</title>
<link href="https://fonts.googleapis.com/css2?family=PT+Sans+Narrow:wght@400;700&family=Open+Sans:wght@400;600&display=swap" rel="stylesheet">
<style>
:root{
  --ink:#2b2b2b;
  --text:#555;
  --brand-blue:#3a63a8;
  --page:#ffffff;
  --rule:#d8d8d8;
  --btn-top:#4a4a4a;
  --btn-bottom:#111;
  --footer:#333333;
  --footer-deep:#222222;
  --footer-text:#cfcfcf;
  --circle:#3a3a3a;
}
*{margin:0;padding:0;box-sizing:border-box}
html,body{width:911px;height:1200px;overflow:hidden;background:var(--page)}
body{position:relative;font-family:"Open Sans",Arial,sans-serif;color:var(--text)}
.abs{position:absolute}
.cond{font-family:"PT Sans Narrow","Arial Narrow",sans-serif}

/* header */
.site-header{left:0;top:0;width:911px;height:118px;background:linear-gradient(#fbfbfb,#efefef);border-top:2px solid var(--brand-blue)}
.header-panel{left:104px;top:0;width:702px;height:118px;background:linear-gradient(#fff,#f6f6f6);box-shadow:0 0 12px rgba(0,0,0,.08)}
.brand{left:122px;top:44px;display:flex;align-items:center;gap:8px;font-family:"PT Sans Narrow",sans-serif;font-size:28px;font-weight:700;color:var(--brand-blue)}
.brand-dot{width:20px;height:20px;border-radius:50%;background:#7a7a7a}
.nav-tab{top:0;height:52px;width:55px;left:611px;background:linear-gradient(#8a8a8a,#555);border-radius:0 0 4px 4px;box-shadow:0 2px 4px rgba(0,0,0,.35);color:#fff;font-size:15px;text-align:center;padding-top:26px}
.nav-link{top:26px;font-size:15px;color:#444}

/* hero */
.hero{left:0;top:118px;width:911px;height:346px;background:linear-gradient(180deg,#3f5a2a 0%,#6e8a4a 30%,#5b8a2a 55%,#3e6a1a 100%)}
.hero-title{left:25px;top:244px;font-size:20px;font-weight:700;color:#fff;text-shadow:0 1px 2px rgba(0,0,0,.6)}
.hero-copy{left:25px;top:274px;width:280px;font-size:8.6px;line-height:15.8px;color:#fff;text-shadow:0 1px 2px rgba(0,0,0,.6)}
.btn{display:block;background:linear-gradient(var(--btn-top),var(--btn-bottom));color:#fff;text-align:center;border-radius:3px;font-family:"PT Sans Narrow",sans-serif}
.hero-more{left:201px;top:358px;width:85px;height:24px;line-height:24px;font-size:13px}
.hero-arrows{left:858px;top:416px}

/* features */
.features{left:0;top:464px;width:911px;height:278px;background:linear-gradient(#fafafa,#f1f1f1);border-bottom:2px solid var(--rule)}
.feature-title{font-size:22px;font-weight:400;color:var(--ink);top:592px}
.feature-copy{top:628px;width:186px;font-size:7.3px;line-height:13.6px;text-align:justify;color:#444}
.feature-more{top:696px;width:67px;height:19px;line-height:19px;font-size:10px}
.icon-fill{left:176px;top:496px;width:57px;height:88px;background:linear-gradient(#f6f6f6,#ececec)}

/* welcome + news */
.section-title{top:776px;font-size:17px;font-weight:700;color:var(--ink);letter-spacing:.2px}
.section-title span{color:var(--brand-blue)}
.welcome-photo{left:129px;top:810px;width:159px;height:97px;border:3px solid #fff;box-shadow:0 0 4px rgba(0,0,0,.35);background:linear-gradient(180deg,#b8c2a0 0%,#e8e8e0 40%,#8aa24a 75%,#4d6a1e 100%)}
.body-copy{font-size:8px;line-height:13.8px;text-align:justify;color:#555}
.dark-btn{background:#3a3a3a;color:#fff;font-family:"PT Sans Narrow",sans-serif;font-size:12px;text-align:center;border:1px solid #222}
.news-arrow{top:779px;width:9px;height:9px}
.news-date{width:44px;height:44px;border-radius:50%;background:var(--circle);color:#fff;font-size:7.5px;text-align:center;line-height:44px;box-shadow:0 0 3px rgba(0,0,0,.4)}

/* footer */
.footer{left:0;top:1026px;width:911px;height:112px;background:var(--footer)}
.footer-col{top:1046px;color:var(--footer-text)}
.footer-col h4{font-weight:400;font-size:10px;margin-bottom:14px;color:#ddd}
.footer-col li{list-style:none;font-size:8px;line-height:13.6px}
.footer-bar{left:0;top:1138px;width:911px;height:62px;background:var(--footer-deep)}
.social{top:1154px;width:20px;height:20px;background:#5a5a5a;border-radius:2px}
.copyright{right:109px;top:1155px;font-size:8px;color:#ddd}
.scale-note{right:109px;top:1174px;font-size:7px;color:#bbb}
</style>
</head>
<body>

<header class="abs site-header"></header>
<div class="abs header-panel"></div>
<div class="abs brand"><span class="brand-dot"></span>Tallow Pinery</div>
<nav>
  <div class="abs nav-tab cond">World</div>
  <div class="abs nav-link cond" style="left:683px">Golf</div>
  <div class="abs nav-link cond" style="left:730px">Club House</div>
</nav>

<section class="abs hero" role="img" aria-label="Golf course photo: golf ball on green grass, flag and golfer in the background"></section>
<h1 class="abs hero-title cond">Cum sociis natoque penatibus et magnis</h1>
<p class="abs hero-copy">Cum sociis natoque penatibus et magnis dis parturient montes, nascetur ridiculus mus. In iaculis facilisis massa. Etiam eu urna. Cum sociis natoque penatibus et magnis dis parturient montes, nascetur ridiculus mus. In iaculis facilisis massa. Etiam eu urna.</p>
<a class="abs btn hero-more">MORE &gt;&gt;</a>
<svg class="abs hero-arrows" width="36" height="32" viewBox="0 0 36 32"><path d="M9 2 Q1 16 9 30" stroke="#fff" stroke-width="3" fill="none"/><path d="M27 2 Q35 16 27 30" stroke="#fff" stroke-width="3" fill="none"/></svg>

<section class="abs features"></section>
<div class="abs icon-fill" role="img" aria-label="Golfer silhouette mid swing"></div>
<svg class="abs" style="left:438px;top:522px" width="52" height="52" viewBox="0 0 52 52">
  <rect x="4" y="6" width="34" height="40" fill="#eee" stroke="#777"/>
  <rect x="4" y="6" width="34" height="6" fill="#555"/>
  <g stroke="#888" stroke-width="1.5"><line x1="9" y1="18" x2="33" y2="18"/><line x1="9" y1="24" x2="28" y2="24"/><line x1="9" y1="30" x2="24" y2="30"/><line x1="9" y1="36" x2="24" y2="36"/></g>
  <circle cx="32" cy="32" r="7" fill="#fff" stroke="#333" stroke-width="2"/>
  <line x1="37" y1="37" x2="45" y2="45" stroke="#333" stroke-width="3"/>
</svg>
<svg class="abs" style="left:677px;top:528px" width="52" height="50" viewBox="0 0 52 50">
  <rect x="2" y="2" width="48" height="46" rx="9" fill="#fff" stroke="#222" stroke-width="2.5"/>
  <rect x="6" y="6" width="40" height="38" rx="6" fill="none" stroke="#222" stroke-width="1.5"/>
  <g stroke="#222" stroke-width="1.5"><line x1="16" y1="15" x2="40" y2="15"/><line x1="16" y1="21" x2="40" y2="21"/><line x1="16" y1="27" x2="40" y2="27"/><line x1="16" y1="33" x2="40" y2="33"/></g>
  <g fill="#222"><circle cx="11" cy="15" r="1.3"/><circle cx="11" cy="21" r="1.3"/><circle cx="11" cy="27" r="1.3"/><circle cx="11" cy="33" r="1.3"/></g>
</svg>

<h2 class="abs feature-title cond" style="left:126px">Collect</h2>
<h2 class="abs feature-title cond" style="left:372px">Analyze</h2>
<h2 class="abs feature-title cond" style="left:614px">Instruct</h2>
<p class="abs feature-copy" style="left:130px">Sed ut perspiciatis unde omnis iste natus error sit voluptatem accusantiumveritatis et quasi architecto beatae vitae dicta sunt.Nemo enim ipsam voluptatem, Nemo enim ipsam voluptatem</p>
<p class="abs feature-copy" style="left:375px">Sed ut perspiciatis unde omnis iste natus error sit voluptatem accusantiumveritatis et quasi architecto beatae vitae dicta sunt.Nemo enim ipsam voluptatem, Nemo enim ipsam voluptatem</p>
<p class="abs feature-copy" style="left:617px">Sed ut perspiciatis unde omnis iste natus error sit voluptatem accusantiumveritatis et quasi architecto beatae vitae dicta sunt.Nemo enim ipsam voluptatem, Nemo enim ipsam voluptatem</p>
<a class="abs btn feature-more" style="left:249px">More &gt;&gt;</a>
<a class="abs btn feature-more" style="left:494px">More &gt;&gt;</a>
<a class="abs btn feature-more" style="left:736px">More &gt;&gt;</a>

<h3 class="abs section-title cond" style="left:127px">WELCOME TO <span>TALLOW PINERY</span></h3>
<div class="abs welcome-photo" role="img" aria-label="Gloved hand placing a golf ball on a tee beside a club"></div>
<p class="abs body-copy" style="left:300px;top:816px;width:250px">Nemo enim ipsam voluptatem quia voluptas sit aspernatur aut odit aut fugit, sed quiaemo enim ipsam voluptatem quia voluptas sit aspernatur aut odit aut fugit, sed quiaSed ut perspiciatis unde omnis iste natus error sit voluptatem accusantium doloremque laudantium, totam rem aperiam, eaque ipsa quae ab illo inventore veritatis et quasi architecto beatae vitae dicta sunt explicabo.</p>
<p class="abs body-copy" style="left:133px;top:922px;width:417px;text-align:left">Sed ut perspiciatis unde omnis iste natus error sit voluptatem accusantium doloremque laudantium, totam rem aperiam, eaque ipsa quae ab illo inventore veritatis et quasi architecto beatae vitae dicta sunt explicabo.</p>
<a class="abs dark-btn" style="left:483px;top:958px;width:62px;height:25px;line-height:24px">learn more</a>

<h3 class="abs section-title cond" style="left:598px">LATEST <span>NEWS</span></h3>
<svg class="abs news-arrow" style="left:776px" viewBox="0 0 9 9"><rect width="9" height="9" fill="#333"/><path d="M6 2 L3 4.5 L6 7" fill="#fff"/></svg>
<svg class="abs news-arrow" style="left:792px" viewBox="0 0 9 9"><rect width="9" height="9" fill="#333"/><path d="M3 2 L6 4.5 L3 7" fill="#fff"/></svg>
<div class="abs news-date" style="left:601px;top:812px">July 4</div>
<p class="abs body-copy" style="left:655px;top:812px;width:147px;line-height:10.8px">Sed ut perspiciatis unde omnis iste natus error sit voluptatem accusantium doloremque laudantium, totam rem ipsa quae ab illo inven.</p>
<div class="abs news-date" style="left:601px;top:874px">July 4</div>
<p class="abs body-copy" style="left:655px;top:874px;width:147px;line-height:10.8px">Sed ut perspiciatis unde omnis iste natus error sit voluptatem accusantium doloremque laudantium, totam rem ipsa quae ab illo inven.</p>
<a class="abs dark-btn" style="left:746px;top:944px;width:61px;height:25px;line-height:24px">learn more</a>

<footer class="abs footer"></footer>
<div class="abs footer-col" style="left:126px"><h4>Tallow Pinery Portal</h4><ul><li>Team Portal</li><li>Tallow Pinery Exchange</li></ul></div>
<div class="abs footer-col" style="left:278px"><h4>Who We Are</h4><ul><li>About us</li><li>Our Company</li><li>Product Development</li></ul></div>
<div class="abs footer-col" style="left:431px"><h4>Outreach</h4><ul><li>Tallow Pinery Attends Harborline Leaders Forum 2013</li><li>Tallow Pinery Attends Ridgeway Venture Summit 2013</li><li>Ready to Tee Up First of Three Product Launches</li><li>Tallow Pinery Attends TechHive Spring 2013</li></ul></div>
<div class="abs footer-col" style="left:690px"><h4>Other Information</h4><ul><li>Privacy Policy</li><li>Terms &amp; Conditions</li></ul></div>

<div class="abs footer-bar"></div>
<div class="abs social" style="left:117px" aria-label="Social link"></div>
<div class="abs social" style="left:146px" aria-label="Social link"></div>
<div class="abs social" style="left:175px" aria-label="Social link"></div>
<div class="abs social" style="left:204px" aria-label="Social link"></div>
<div class="abs social" style="left:233px" aria-label="Social link"></div>
<svg class="abs" style="left:262px;top:1154px" width="20" height="20" viewBox="0 0 20 20"><rect width="20" height="20" rx="2" fill="#5a5a5a"/><rect x="4" y="6" width="12" height="8" fill="none" stroke="#ddd"/><path d="M4 6 L10 11 L16 6" fill="none" stroke="#ddd"/></svg>
<p class="abs copyright">Copyright © 2013 tallow-pinery.com. All rights reserved.</p>
<p class="abs scale-note">x2</p>

</body>
</html>
```